New Dental Office Needs an Attractive and user friendly Website Designed

I need a website for a new dental office. The Name is Harrowfield Dentistry. I would like a Modern design with a user friendly interface and usability.
I would like a landing page, a page that lists the services we offer: Cosmetic Dentistry, Implants, Dental Hygiene, Emergency Services, Restorations, Dentures
Target Market(s)
Mid to upper class
Industry/Entity Type
Dentistry
Coding
Number of Pages Required
1 page
Requirements
Must have
- Landing page that has a scheduling option, Procedures, operating hours, and contact us info
Nice to have
- Appealing design, Soft comforting colors. Easy to navigate page, Modern and professional.

```html
<!DOCTYPE html>
<html lang="en">
<head>
<meta charset="utf-8">
<title>Harrowfield Dentistry</title>
<link rel="stylesheet" href="https://fonts.googleapis.com/css2?family=Libre+Baskerville:wght@400;700&family=Montserrat:wght@400;500;600;700&display=swap">
<style>
:root{
  --blue:#0b8fd3;
  --blue-dark:#0a6fae;
  --navy:#0d2b3e;
  --ink:#1c1c1c;
  --text:#4a4a4a;
  --pale:#e8f4fb;
  --white:#ffffff;
  --star:#f2a91d;
  --hero-a:#1d5f7e;
  --hero-b:#6fa9c6;
  --serif:"Libre Baskerville",Georgia,serif;
  --sans:"Montserrat",Arial,sans-serif;
}
*{box-sizing:border-box;margin:0;padding:0}
html,body{width:1200px;height:4030px;overflow:hidden}
body{font-family:var(--sans);color:var(--ink);background:var(--white);position:relative}
.abs{position:absolute}
section{position:absolute;left:0;width:1200px}

/* hero */
.hero{top:0;height:685px;background:linear-gradient(100deg,var(--hero-a) 0%,#2f7598 45%,var(--hero-b) 100%)}
.hero-photo{position:absolute;right:0;top:42px;width:620px;height:643px;background:radial-gradient(ellipse at 60% 45%,#bcd8e6 0%,#7fb1cb 45%,rgba(79,140,172,0) 75%)}
.topbar{top:0;left:0;width:1200px;height:42px;background:rgba(13,43,62,.55);color:var(--white);font-size:13px;font-weight:600}
.topbar .item{position:absolute;top:8px;display:flex;align-items:center;gap:12px}
.topbar .ico{width:28px;height:28px;border-radius:50%;background:var(--white);display:flex;align-items:center;justify-content:center}
.logo{font-family:var(--serif);color:var(--white);text-align:center;line-height:1}
.logo .name{font-size:34px}
.logo .sub{font-size:15px;letter-spacing:6px;margin-top:6px}
.nav{top:58px;left:0;width:1200px}
.nav .links{position:absolute;left:347px;top:20px;display:flex;gap:30px;font-size:13px;font-weight:600;color:var(--white)}
.nav .links .on{color:#39a9e8}
.btn{display:flex;align-items:center;justify-content:center;font-weight:700;font-size:15px;color:var(--white);background:var(--blue);border-radius:4px}
.hero-kicker{left:112px;top:190px;font-size:23px;font-weight:500;color:#2aa0e6}
.hero h1{position:absolute;left:110px;top:225px;font-family:var(--serif);font-weight:700;font-size:64px;line-height:68px;color:var(--white)}
.hero-lead{left:114px;top:372px;font-size:19px;line-height:27px;color:var(--white);width:480px}
.hero-btn{left:111px;top:446px;width:278px;height:49px;border:2px solid var(--white);border-radius:6px;background:transparent}
.rating{left:110px;top:520px;font-size:19px;font-weight:600;color:var(--white);display:flex;gap:12px;align-items:center}
.rating .stars{color:var(--star);font-size:16px;letter-spacing:2px}

/* about */
.about{top:685px;height:681px}
.about-ring{left:114px;top:105px;width:460px;height:460px;border-radius:50%;border:12px solid var(--blue);border-right-color:transparent;transform:rotate(20deg)}
.about-photo{left:128px;top:115px;width:446px;height:446px;border-radius:50%;background:radial-gradient(circle at 50% 40%,#f3d9c6 0%,#d7b49a 35%,#a9c8da 75%)}
.tooth-badge{left:444px;top:433px;width:136px;height:136px;border-radius:50%;background:var(--white);border:4px solid var(--blue);display:flex;align-items:center;justify-content:center}
.kicker{font-size:21px;font-weight:500;color:var(--blue)}
.about .kicker{position:absolute;left:631px;top:100px}
.about h2{position:absolute;left:628px;top:138px;font-family:var(--serif);font-weight:400;font-size:40px;line-height:49px;color:var(--ink)}
.about p{position:absolute;left:632px;top:250px;width:415px;font-size:13.5px;line-height:28.4px;color:var(--text)}
.about .btn{position:absolute;left:631px;top:531px;width:158px;height:46px}

/* procedures */
.procedures{top:1366px;height:571px;background:var(--pale)}
.center{position:absolute;left:0;width:1200px;text-align:center}
.sec-title{font-family:var(--serif);font-weight:400;font-size:42px;color:var(--ink)}
.card{position:absolute;top:188px;width:299px;height:283px;background:var(--white);border-radius:6px;padding:20px 26px}
.card .ico{width:78px;height:78px;border-radius:50%;background:#cfe8f6;display:flex;align-items:center;justify-content:center}
.card h3{margin-top:30px;font-size:19px;font-weight:700}
.card p{margin-top:16px;font-size:13.5px;line-height:27px;color:var(--text)}
.card .go{position:absolute;left:28px;top:216px}
.slide-arrow{position:absolute;top:1683px}

/* stats */
.stats{top:1937px;height:277px;background:var(--blue);color:var(--white)}
.stat{position:absolute;top:78px;width:260px;text-align:center}
.stat .num{font-size:46px;font-weight:600}
.stat .lbl{margin-top:22px;font-size:20px;font-weight:600}

/* testimonials */
.testimonials{top:2214px;height:830px}
.tcard{position:absolute;top:223px;width:453px;height:444px;background:var(--white);box-shadow:0 0 10px rgba(0,0,0,.14);text-align:center;padding-top:60px}
.quote{position:absolute;top:-42px;left:184px;width:84px;height:84px;border-radius:50%;background:var(--blue);color:var(--white);font-family:var(--serif);font-size:82px;line-height:118px;font-weight:700}
.tcard .stars{color:var(--star);font-size:24px;letter-spacing:4px}
.tcard p{margin:16px auto 0;width:380px;font-size:14.5px;line-height:28.4px;color:var(--text)}
.avatar{margin:18px auto 0;width:92px;height:92px;border-radius:50%;background:radial-gradient(circle at 50% 45%,#e2c3a9,#b68d6e)}
.tcard .who{margin-top:12px;font-size:17px;font-weight:700;color:var(--navy)}
.tcard .role{margin-top:8px;font-size:15px;color:var(--text)}
.dots{position:absolute;top:718px;left:568px;display:flex;gap:11px}
.dots span{width:14px;height:14px;border-radius:50%;border:2px solid var(--navy)}
.dots span.on{background:var(--navy)}

/* appointment */
.appointment{top:3044px;height:676px;background:var(--pale)}
.contact{position:absolute;left:112px}
.contact .circ{position:absolute;left:0;width:62px;height:62px;border-radius:50%;background:var(--blue);display:flex;align-items:center;justify-content:center}
.contact h4{position:absolute;left:82px;font-size:21px;font-weight:600;color:var(--blue);white-space:nowrap}
.contact .txt{position:absolute;left:84px;font-size:15px;line-height:28px;color:var(--text);white-space:nowrap}
.field{position:absolute;background:var(--white);border-radius:4px;height:45px;display:flex;align-items:center;justify-content:space-between;padding:0 18px;font-size:14px;color:var(--text)}
.flabel{position:absolute;font-size:14px;color:var(--text)}

/* footer */
.footer{top:3720px;height:310px;background:var(--blue);color:var(--white)}
.footer .links{position:absolute;top:183px;left:0;width:1200px;display:flex;justify-content:center;gap:46px;font-size:15px;font-weight:500}
.footer .rule{position:absolute;top:235px;left:111px;width:978px;height:1px;background:rgba(255,255,255,.6)}
.footer .copy{position:absolute;top:258px;left:0;width:1200px;text-align:center;font-size:15px}
</style>
</head>
<body>

<section class="hero">
  <div class="hero-photo" role="img" aria-label="Smiling dentist in blue gloves lowering her mask in a bright treatment room"></div>

  <div class="abs topbar">
    <div class="item" style="left:111px">
      <span class="ico"><svg width="18" height="18" viewBox="0 0 24 24" fill="none" stroke="#0b8fd3" stroke-width="2"><circle cx="12" cy="12" r="9"/><path d="M12 7v5l3 2"/></svg></span>
      Working Hours Mon - fri 9.00 AM To 6.00 PM
    </div>
    <div class="item" style="left:517px">
      <span class="ico"><svg width="16" height="16" viewBox="0 0 24 24" fill="#0b8fd3"><path d="M6.6 10.8a15 15 0 006.6 6.6l2.2-2.2a1 1 0 011-.25 11 11 0 003.6.6 1 1 0 011 1V20a1 1 0 01-1 1A17 17 0 013 4a1 1 0 011-1h3.5a1 1 0 011 1 11 11 0 00.6 3.6 1 1 0 01-.25 1z"/></svg></span>
      Call (555) 318-2047
    </div>
    <div class="item" style="left:733px">
      <span class="ico"><svg width="17" height="17" viewBox="0 0 24 24" fill="none" stroke="#0b8fd3" stroke-width="2"><rect x="3" y="5" width="18" height="14" rx="1"/><path d="M3 6l9 7 9-7"/></svg></span>
      Mail hello@harrowfieldcare.com
    </div>
  </div>

  <div class="abs nav">
    <div class="abs logo" style="left:104px;top:0">
      <div class="name">Harrowfield</div>
      <div class="sub">DENTISTRY</div>
    </div>
    <div class="links">
      <span class="on">HOME</span><span>ABOUT US</span><span>PROCEDURES</span><span>TEAM</span><span>CONTACT US</span>
    </div>
    <div class="abs btn" style="left:820px;top:4px;width:268px;height:47px">Schedule an Appointment</div>
  </div>

  <div class="abs hero-kicker">Harrowfield Dentistry</div>
  <h1>Bright Smiles.<br>Better Care.</h1>
  <div class="abs hero-lead">From cleanings to cosmetic care, we keep your smile shining.</div>
  <div class="abs btn hero-btn">Schedule an Appointment</div>
  <div class="abs rating">ReviewHub Rating 5.0 <span class="stars">★★★★★</span> Based on 1k Reviews</div>
</section>

<section class="about">
  <div class="abs about-ring"></div>
  <div class="abs about-photo" role="img" aria-label="Smiling woman in the dental chair during a check-up"></div>
  <div class="abs tooth-badge">
    <svg width="80" height="80" viewBox="0 0 64 64" fill="#0b8fd3"><path d="M14 14c6-5 12-2 16 0 4-2 10-5 16 0 5 5 3 14 0 20-2 4-2 10-4 17-1 4-5 4-6 0l-3-12c-1-3-3-3-4 0l-3 12c-1 4-5 4-6 0-2-7-2-13-4-17-3-6-5-15-2-20z"/><path d="M50 4l2 5 5 2-5 2-2 5-2-5-5-2 5-2zM57 18l1 3 3 1-3 1-1 3-1-3-3-1 3-1z"/></svg>
  </div>
  <div class="kicker">About Us</div>
  <h2>Your Local<br>Smile Experts</h2>
  <p>Lorem Ipsum is simply dummy text of the printing and typesetting industry. Lorem Ipsum has been the industry's standard dummy text ever since the 1500s, when an unknown printer took a galley of type and scrambled it to make a type specimen book. It has survived not only five centuries, but also the leap into electronic typesetting, remaining essentially unchanged. It was popularised in the 1960s with the release of Letraset sheets containing Lorem Ipsum passages</p>
  <div class="btn">Read More</div>
</section>

<section class="procedures">
  <div class="center kicker" style="top:72px">Our Procedures</div>
  <div class="center sec-title" style="top:110px">Comprehensive Dental Services</div>

  <div class="card" style="left:111px">
    <div class="ico"><svg width="44" height="44" viewBox="0 0 48 48" fill="none" stroke="#1c3d52" stroke-width="2"><path d="M8 12c4-4 9-2 12 0 3-2 8-4 12 0 3 4 2 10 0 15-1 4-1 8-3 13-1 3-4 3-4 0l-2-9c-1-2-3-2-3 0l-2 9c-1 3-3 3-4 0-2-5-2-9-3-13-3-5-4-11-3-15z"/><path d="M38 8v30M35 8h6M38 38l-2 4h4z"/></svg></div>
    <h3>Cosmetic Dentistry</h3>
    <p>Teeth Whitening, Veneers, Smile Makeovers</p>
    <svg class="go" width="38" height="38" viewBox="0 0 38 38" fill="none" stroke="#0d2b3e" stroke-width="2"><circle cx="19" cy="19" r="17"/><path d="M11 19h15M20 13l6 6-6 6"/></svg>
  </div>
  <div class="card" style="left:451px">
    <div class="ico"><svg width="46" height="44" viewBox="0 0 50 48" fill="none" stroke="#1c3d52" stroke-width="2"><path d="M6 24c0-6 3-8 6-6 2-2 4-2 6 0 2-2 4-2 6 0 2-2 4-2 6 0 2-2 4-2 6 0 3-2 6 0 6 6v8c0 3-3 4-5 2-2 2-4 2-6 0-2 2-4 2-6 0-2 2-4 2-6 0-2 2-4 2-6 0-2 2-5 1-5-2z"/><path d="M22 4h6v6h-6zM25 10v8"/></svg></div>
    <h3>Implants</h3>
    <p>Permanent tooth replacement with natural look and feel</p>
    <svg class="go" width="38" height="38" viewBox="0 0 38 38" fill="none" stroke="#0d2b3e" stroke-width="2"><circle cx="19" cy="19" r="17"/><path d="M11 19h15M20 13l6 6-6 6"/></svg>
  </div>
  <div class="card" style="left:789px">
    <div class="ico"><svg width="46" height="44" viewBox="0 0 50 48" fill="none" stroke="#1c3d52" stroke-width="2"><path d="M6 18c4-6 10-4 13-2 2-2 6-2 8 0 3-2 9-4 13 2 3 5 0 10-2 12-1 4-2 8-4 10-2 2-4 1-4-2l-1-6h-8l-1 6c0 3-2 4-4 2-2-2-3-6-4-10-2-2-5-7-2-12z"/><path d="M4 24h42M10 10l3 3M25 6v4M40 10l-3 3"/></svg></div>
    <h3>Dental Hygiene</h3>
    <p>Routine cleanings, fluoride treatments, and oral health checks</p>
    <svg class="go" width="38" height="38" viewBox="0 0 38 38" fill="none" stroke="#0d2b3e" stroke-width="2"><circle cx="19" cy="19" r="17"/><path d="M11 19h15M20 13l6 6-6 6"/></svg>
  </div>
</section>
<svg class="slide-arrow" style="left:48px" width="36" height="36" viewBox="0 0 36 36" fill="none" stroke="#1c1c1c" stroke-width="2"><circle cx="18" cy="18" r="16"/><path d="M21 11l-7 7 7 7"/></svg>
<svg class="slide-arrow" style="left:1115px" width="36" height="36" viewBox="0 0 36 36" fill="none" stroke="#0b8fd3" stroke-width="2"><circle cx="18" cy="18" r="16"/><path d="M15 11l7 7-7 7"/></svg>

<section class="stats">
  <div class="stat" style="left:98px"><div class="num">1000+</div><div class="lbl">Happy Patients</div></div>
  <div class="stat" style="left:348px"><div class="num">250+</div><div class="lbl">Teeth Whitened</div></div>
  <div class="stat" style="left:591px"><div class="num">800+</div><div class="lbl">Dental Implants</div></div>
  <div class="stat" style="left:833px"><div class="num">15+</div><div class="lbl">Years of Experience</div></div>
</section>

<section class="testimonials">
  <div class="center kicker" style="top:72px">Our Testimonials</div>
  <div class="center sec-title" style="top:114px">Our Happy Customers</div>

  <div class="tcard" style="left:120px">
    <div class="quote">“</div>
    <div class="stars">★★★★★</div>
    <p>Lorem Ipsum is simply dummy text of the printing and typesetting industry. Lorem Ipsum has been the industry's standard dummy text ever since the 1500s, when an unknown printer took a galley of type and scrambled it to make a type specimen</p>
    <div class="avatar" role="img" aria-label="Portrait of patient Claire Whitmore"></div>
    <div class="who">Claire Whitmore</div>
    <div class="role">Client</div>
  </div>
  <div class="tcard" style="left:621px">
    <div class="quote">“</div>
    <div class="stars">★★★★★</div>
    <p>Lorem Ipsum is simply dummy text of the printing and typesetting industry. Lorem Ipsum has been the industry's standard dummy text ever since the 1500s, when an unknown printer took a galley of type and scrambled it to make a type specimen</p>
    <div class="avatar" role="img" aria-label="Portrait of patient Daniel"></div>
    <div class="who">Daniel</div>
    <div class="role">Client</div>
  </div>
  <div class="dots"><span class="on"></span><span></span><span></span></div>
</section>

<section class="appointment">
  <div class="center kicker" style="top:80px">Schedule Appointment</div>
  <div class="center sec-title" style="top:126px">Book An Appointment</div>
  <div class="center" style="top:193px;font-size:13.5px;color:var(--text)">Lorem Ipsum is simply dummy text of the printing and typesetting industry.</div>

  <div class="contact" style="top:247px">
    <div class="circ" style="top:0"><svg width="30" height="30" viewBox="0 0 24 24" fill="none" stroke="#fff" stroke-width="1.5"><path d="M6.6 10.8a15 15 0 006.6 6.6l2.2-2.2a1 1 0 011-.25 11 11 0 003.6.6 1 1 0 011 1V20a1 1 0 01-1 1A17 17 0 013 4a1 1 0 011-1h3.5a1 1 0 011 1 11 11 0 00.6 3.6 1 1 0 01-.25 1z"/></svg></div>
    <h4 style="top:4px">Call Us</h4>
    <div class="txt" style="top:34px">(555) 318-2047 /( 555) 604-1193</div>
  </div>
  <div class="contact" style="top:334px">
    <div class="circ" style="top:0"><svg width="30" height="30" viewBox="0 0 24 24" fill="none" stroke="#fff" stroke-width="1.5"><path d="M12 22s7-7 7-12a7 7 0 00-14 0c0 5 7 12 7 12z"/><circle cx="12" cy="10" r="2.5"/></svg></div>
    <h4 style="top:4px">Location</h4>
    <div class="txt" style="top:34px">Harrowfield Dentistry<br>2025, Lorem Ipsum is simply<br>NY 2154</div>
  </div>
  <div class="contact" style="top:470px">
    <div class="circ" style="top:0"><svg width="32" height="32" viewBox="0 0 24 24" fill="none" stroke="#fff" stroke-width="1.5"><circle cx="12" cy="12" r="9"/><path d="M12 6v6l4 3"/></svg></div>
    <h4 style="top:-6px">Working Hours</h4>
    <div class="txt" style="top:26px">Monday To Friday 9.00 AM - 6.00 PM<br>Saturday And Sunday Holiday</div>
  </div>

  <div class="field" style="left:621px;top:249px;width:446px">Your Name</div>
  <div class="field" style="left:621px;top:308px;width:446px">Phone Number</div>
  <div class="field" style="left:621px;top:367px;width:446px">Select Services</div>
  <div class="flabel" style="left:639px;top:427px">Choose Date</div>
  <div class="flabel" style="left:866px;top:427px">Choose Time</div>
  <div class="field" style="left:621px;top:458px;width:213px">22/05/2025
    <svg width="22" height="22" viewBox="0 0 24 24" fill="none" stroke="#555" stroke-width="1.5"><rect x="3" y="5" width="18" height="16" rx="1"/><path d="M3 10h18M8 3v4M16 3v4M7 14h2M11 14h2M15 14h2M7 17h2M11 17h2M15 17h2"/></svg></div>
  <div class="field" style="left:848px;top:458px;width:216px">10.00 AM
    <svg width="22" height="22" viewBox="0 0 24 24" fill="none" stroke="#555" stroke-width="1.5"><circle cx="12" cy="12" r="9"/><path d="M12 7v5l3 2"/></svg></div>
  <div class="abs btn" style="left:663px;top:535px;width:359px;height:45px">Schedule an Appointment</div>
</section>

<section class="footer">
  <div class="abs logo" style="left:0;width:1200px;top:78px">
    <div class="name" style="font-size:44px">Harrowfield</div>
    <div class="sub" style="font-size:19px;letter-spacing:8px">DENTISTRY</div>
  </div>
  <div class="links"><span>HOME</span><span>ABOUT US</span><span>PROCEDURES</span><span>TEAM</span><span>CONTACT US</span></div>
  <div class="rule"></div>
  <div class="copy">Copyrights@2025 . Harrowfield Dentistry .All Rights Reserved</div>
</section>

</body>
</html>
```